Mosquito and outdoor pest management

The uploaded logo must be integrated as the main theme of the card. I would like it to be modern and eye catching. Maybe some backround images or light silver metallic background.
Space enough at the base for contact info to be put in- phone numbers,emails,names,website.
Space on the back for short blog and lines for hand writing..calling card.
Commercial- golf courses, schools, outdoor function properties, pre event treatments.
Residential- retirement villages, townhome complexes and general houses
Management

```html
<!DOCTYPE html>
<html lang="en">
<head>
<meta charset="utf-8">
<title>Bayline Pest Co – Business Card</title>
<link rel="stylesheet" href="https://fonts.googleapis.com/css2?family=Cinzel:wght@400;500&display=swap">
<style>
  :root {
    --backdrop: #3b3b3b;
    --silver-light: #f7f7f7;
    --silver-mid: #dcdcdc;
    --silver-dark: #b9b9b9;
    --brand-red: #e8212c;
    --ink: #141414;
    --text-grey: #4a4a4a;
    --rule-grey: #7d7d7d;
  }
  * { box-sizing: border-box; margin: 0; padding: 0; }
  html, body {
    width: 1105px;
    height: 1200px;
    overflow: hidden;
    background: var(--backdrop);
    font-family: "Cinzel", serif;
  }
  .canvas {
    position: relative;
    width: 1105px;
    height: 1200px;
  }
  .card {
    position: absolute;
    left: 192px;
    width: 720px;
    height: 412px;
    overflow: hidden;
    background: radial-gradient(ellipse at 45% 45%, var(--silver-light) 0%, var(--silver-mid) 60%, var(--silver-dark) 100%);
    box-shadow: 0 4px 14px rgba(0,0,0,0.45);
  }
  .card-front { top: 146px; }
  .card-back { top: 602px; }

  /* Front */
  .holder-name {
    position: absolute;
    left: 44px;
    top: 46px;
    font-size: 26px;
    font-weight: 500;
    color: var(--brand-red);
    letter-spacing: 0.5px;
  }
  .holder-title {
    position: absolute;
    left: 44px;
    top: 82px;
    font-size: 19px;
    color: var(--ink);
  }
  .contact-list {
    position: absolute;
    left: 44px;
    top: 122px;
    list-style: none;
  }
  .contact-item {
    display: flex;
    align-items: center;
    height: 31px;
    font-size: 17px;
    color: var(--text-grey);
  }
  .contact-icon {
    width: 16px;
    height: 16px;
    margin-right: 14px;
    flex: none;
  }
  .front-illustration {
    position: absolute;
    right: 0;
    top: 0;
    width: 720px;
    height: 412px;
  }
  .company-name {
    position: absolute;
    font-size: 40px;
    font-weight: 400;
    color: var(--ink);
    white-space: nowrap;
    line-height: 1;
  }
  .card-front .company-name {
    left: 50px;
    top: 300px;
  }

  /* Back */
  .writing-lines {
    position: absolute;
    left: 26px;
    top: 0;
    width: 659px;
    height: 280px;
  }
  .card-back .company-name {
    left: 26px;
    top: 312px;
  }
</style>
</head>
<body>
<main class="canvas">

  <section class="card card-front" aria-label="Business card front">
    <svg class="front-illustration" viewBox="0 0 720 412" role="img" aria-label="Large red and black mosquito illustration filling the right side of the card">
      <defs>
        <linearGradient id="illustrationTone" x1="0" y1="0" x2="1" y2="1">
          <stop offset="0" stop-color="#e8212c"/>
          <stop offset="0.55" stop-color="#b0141c"/>
          <stop offset="1" stop-color="#0d0d0d"/>
        </linearGradient>
      </defs>
      <path d="M553 0 H720 V412 H480 C490 330 480 260 530 200 C550 150 565 80 553 0 Z" fill="url(#illustrationTone)"/>
    </svg>

    <h1 class="holder-name">Alex Morgan</h1>
    <p class="holder-title">CEO/Founder</p>

    <ul class="contact-list">
      <li class="contact-item">
        <svg class="contact-icon" viewBox="0 0 16 16" aria-hidden="true">
          <path d="M3.5 1.5 L6 4 L4.8 5.8 C5.6 7.8 8.2 10.4 10.2 11.2 L12 10 L14.5 12.5 L12.8 14.4 C8 14 2 8 1.6 3.2 Z" fill="var(--brand-red)"/>
        </svg>
        555 204 7319
      </li>
      <li class="contact-item">
        <svg class="contact-icon" viewBox="0 0 16 16" aria-hidden="true">
          <rect x="1" y="3.5" width="14" height="9" fill="var(--brand-red)"/>
          <path d="M1.5 4 L8 9 L14.5 4" fill="none" stroke="#fff" stroke-width="1.2"/>
        </svg>
        hello@baylinepest.com
      </li>
      <li class="contact-item">
        <svg class="contact-icon" viewBox="0 0 16 16" aria-hidden="true">
          <circle cx="8" cy="8" r="7" fill="var(--brand-red)"/>
          <path d="M1.5 8 H14.5 M8 1 C5 4 5 12 8 15 M8 1 C11 4 11 12 8 15" fill="none" stroke="#fff" stroke-width="1"/>
        </svg>
        www.baylinepest.com
      </li>
    </ul>

    <p class="company-name">Bayline Pest Co</p>
  </section>

  <section class="card card-back" aria-label="Business card back">
    <svg class="writing-lines" viewBox="0 0 659 280" aria-hidden="true">
      <g stroke="var(--rule-grey)" stroke-width="1.3" stroke-dasharray="2 3">
        <line x1="0" y1="57" x2="659" y2="57"/>
        <line x1="0" y1="108" x2="659" y2="108"/>
        <line x1="0" y1="157" x2="659" y2="157"/>
        <line x1="0" y1="209" x2="659" y2="209"/>
        <line x1="0" y1="262" x2="659" y2="262"/>
      </g>
    </svg>

    <p class="company-name">Bayline Pest Co</p>
  </section>

</main>
</body>
</html>
```